New Bicycle shop business card

Hi!
I'm looking for a business card for my new proffesional bike mechanics shop. This shop is only for fixing broken bikes and not selling bikes.
Peferbly a modern and sleek and modern design.
Colors: black, grey, red, white
Information:
Name: Rijwielwerkplaats Vanhoutte
Shop owner: Bart Vanhoutte & Marieke Segers
Website: www.rijwielwerkplaats-vanhoutte.be
Email: info@rijwielwerkplaats-vanhoutte.be
Phone number: +32471902368
Street adres: Kerkweg 46
9940 Bellebeke
Slogan/shop information: Herstellingen van alle merken.
Logo: see files.
Target Market(s)
People who seek a mechanic to fix or upgrade their bikes.
Contact Information for Business Card
Information:
Website: info@rijwielwerkplaats-vanhoutte.be
9940 Bellebeke
Logo: see files.

```html
<!DOCTYPE html>
<html lang="nl">
<head>
<meta charset="utf-8">
<title>Rijwielwerkplaats Vanhoutte – visitekaartje</title>
<link rel="stylesheet" href="https://fonts.googleapis.com/css2?family=Lato:wght@300;400;700;900&display=swap">
<style>
  :root {
    --backdrop: #e4e4e4;
    --card-white: #ffffff;
    --card-red: #e0123e;
    --ink: #1d1b1b;
    --ink-soft: #3a3a3a;
    --rule-grey: #c9c9c9;
    --rule-white: rgba(255,255,255,0.75);
    --text-white: #ffffff;
  }
  * { box-sizing: border-box; margin: 0; padding: 0; }
  html, body {
    width: 1200px; height: 900px; overflow: hidden;
    background: var(--backdrop);
    font-family: "Lato", Arial, sans-serif;
  }
  .stage {
    width: 1200px; height: 900px;
    display: flex; align-items: center; justify-content: center; gap: 48px;
  }
  .card {
    width: 530px; height: 340px;
    border-radius: 26px;
    display: flex; flex-direction: column; align-items: center; justify-content: center;
    text-align: center;
    box-shadow: 0 10px 24px rgba(0,0,0,0.12);
  }
  .card--front { background: var(--card-white); color: var(--ink); }
  .card--back { background: var(--card-red); color: var(--text-white); }

  .brand { display: flex; align-items: center; gap: 12px; }
  .brand__mark { width: 16px; height: 16px; background: var(--card-red); }
  .brand__name {
    font-weight: 900; text-transform: uppercase;
    font-size: 26px; line-height: 1.1; letter-spacing: 1.5px;
  }
  .card--front .brand__name { color: var(--ink); }
  .card--back .brand__name { color: var(--text-white); font-size: 28px; }

  .tagline {
    margin-top: 14px; font-size: 13px; letter-spacing: 0.6px;
    text-transform: uppercase; color: var(--ink-soft);
    padding-bottom: 12px; border-bottom: 1px solid var(--rule-grey);
    width: 300px;
  }
  .address {
    margin-top: 12px; font-size: 15px; color: var(--ink);
    padding-top: 12px; border-top: 1px solid var(--rule-grey); width: 300px;
  }

  .rule { width: 180px; height: 1px; background: var(--rule-white); margin: 14px 0; }
  .owners { font-weight: 700; font-size: 17px; text-transform: uppercase; letter-spacing: 0.3px; }
  .role { font-weight: 300; font-size: 13px; margin-top: 2px; }
  .phone { font-weight: 400; font-size: 14px; }
  .contact { font-weight: 400; font-size: 12.5px; margin-top: 28px; }
</style>
</head>
<body>
<main class="stage">
  <section class="card card--front" aria-label="Voorkant visitekaartje">
    <div class="brand">
      <span class="brand__mark"></span>
      <span class="brand__name">Rijwielwerkplaats<br>Vanhoutte</span>
    </div>
    <p class="tagline">Herstellingen van alle merken</p>
    <p class="address">Kerkweg 46 9940 Bellebeke</p>
  </section>

  <section class="card card--back" aria-label="Achterkant visitekaartje">
    <div class="brand">
      <span class="brand__name">Rijwielwerkplaats<br>Vanhoutte</span>
    </div>
    <div class="rule"></div>
    <p class="owners">Bart Vanhoutte &amp; Marieke Segers</p>
    <p class="role">Owner</p>
    <div class="rule"></div>
    <p class="phone">+32471902368</p>
    <p class="contact">E: info@rijwielwerkplaats-vanhoutte.be | W: www.rijwielwerkplaats-vanhoutte.be</p>
  </section>
</main>
</body>
</html>
```